Dunmore Roofing

Want a professional looking business card

Industry/Entity Type

Business

Contact Information for Business Card

Paul Dunmore ( Owner) paul@dunmoreroofing-example.com, www.dunmoreroofing-example.com, Adress: 4172 Township road 43 Alderbrook,NB K9X4T2

```html
<!DOCTYPE html>
<html lang="en">
<head>
<meta charset="utf-8">
<title>Dunmore Roofing – Business Card</title>
<link rel="stylesheet" href="https://fonts.googleapis.com/css2?family=Roboto:wght@400;700;900&family=Roboto+Condensed:wght@400;500&display=swap">
<style>
  :root {
    --backdrop: #262626;
    --card-white: #f2f2f2;
    --brand-blue: #173f7d;
    --text-grey: #4a4a4a;
    --white: #ffffff;
  }
  * { margin: 0; padding: 0; box-sizing: border-box; }
  html, body { width: 1200px; height: 960px; overflow: hidden; }
  body {
    background: var(--backdrop);
    position: relative;
    font-family: "Roboto", Arial, sans-serif;
  }
  .card {
    position: absolute;
    width: 600px;
    height: 343px;
    box-shadow: 0 3px 8px rgba(0,0,0,0.45);
  }
  .card--front { left: 314px; top: 113px; background: var(--card-white); }
  .card--back { left: 311px; top: 472px; background: var(--brand-blue); }

  .wordmark {
    position: absolute;
    font-family: "Roboto", Arial, sans-serif;
    font-weight: 900;
    text-transform: uppercase;
    line-height: 1.1;
  }
  .card--front .wordmark {
    left: 39px; top: 98px;
    color: var(--brand-blue);
    font-size: 28px;
    letter-spacing: 2px;
  }
  .card--back .wordmark {
    left: 0; right: 0; top: 176px;
    text-align: center;
    color: var(--white);
    font-size: 34px;
    letter-spacing: 3px;
  }

  .contact {
    position: absolute;
    left: 39px; top: 200px;
    color: var(--text-grey);
    font-size: 14.5px;
    line-height: 19px;
  }
  .contact__address { margin-bottom: 7px; }
  .contact__row { display: flex; align-items: center; gap: 8px; }
  .contact__icon { width: 14px; height: 14px; fill: var(--brand-blue); flex: none; }

  .name-band {
    position: absolute;
    left: 371px; top: 217px;
    width: 229px; height: 72px;
  }
  .name-band svg { position: absolute; inset: 0; }
  .name-band__text {
    position: absolute;
    right: 21px; top: 12px;
    text-align: right;
    color: var(--white);
    font-family: "Roboto Condensed", Arial, sans-serif;
  }
  .name-band__name { font-size: 23px; font-weight: 500; line-height: 27px; text-transform: uppercase; }
  .name-band__role { font-size: 16px; line-height: 20px; text-transform: uppercase; }

  .card__url {
    position: absolute;
    left: 0; right: 0; top: 284px;
    text-align: center;
    color: var(--white);
    font-size: 15px;
    letter-spacing: 4px;
  }
</style>
</head>
<body>

<section class="card card--front">
  <div class="wordmark">Dunmore<br>Roofing</div>

  <div class="contact">
    <p class="contact__address">4172 Township road 43<br>Alderbrook, NB K9X4T2</p>
    <p class="contact__row">
      <svg class="contact__icon" viewBox="0 0 24 24"><path d="M6.6 10.8a15.1 15.1 0 0 0 6.6 6.6l2.2-2.2a1 1 0 0 1 1-.25 11.4 11.4 0 0 0 3.6.57 1 1 0 0 1 1 1V20a1 1 0 0 1-1 1A17 17 0 0 1 3 4a1 1 0 0 1 1-1h3.5a1 1 0 0 1 1 1c0 1.25.2 2.45.57 3.57a1 1 0 0 1-.25 1z"/></svg>
      613 555 0148
    </p>
    <p class="contact__row">
      <svg class="contact__icon" viewBox="0 0 24 24"><path d="M2 6.5V19h20V6.5l-10 7z M2 5h20l-10 7z"/></svg>
      paul@dunmoreroofing-example.com
    </p>
    <p class="contact__row">
      <svg class="contact__icon" viewBox="0 0 24 24"><circle cx="12" cy="12" r="10"/><path d="M7 8c2 0 3 1 3 2.5S9 13 10 14.5 11 18 11 19M15 5c0 2-1 3-2 3s-1 2 1 2 3 1 3 3" fill="none" stroke="#f2f2f2" stroke-width="1.6"/></svg>
      www.dunmoreroofing-example.com
    </p>
  </div>

  <div class="name-band">
    <svg viewBox="0 0 229 72" width="229" height="72"><polygon points="0,0 229,0 229,72 63,72" fill="#173f7d"/></svg>
    <div class="name-band__text">
      <p class="name-band__name">Paul Dunmore</p>
      <p class="name-band__role">Owner</p>
    </div>
  </div>
</section>

<section class="card card--back">
  <div class="wordmark">Dunmore<br>Roofing</div>
  <p class="card__url">www.dunmoreroofing-example.com</p>
</section>

</body>
</html>
```